Seed Oil Safety Card for Healthy Restaurant Dining

I am seeking a design for a physical card to communicate my wife's health-related dietary restriction regarding seed oils. This card will be given to restaurant waiters to ensure her meals are prepared without seed oils, as it is a health issue and not merely a preference.
My wife cannot eat any “seed oil” or “processed oil”, including:
- Vegetable oil
- Canola oil
- Soybean oil
- Sunflower oil
- Corn oil
- Cottonseed oil
- Safflower oil
- Peanut oil
- Sesame oil
Oils that are OK for her to consume:
- Butter (most preferable)
- Extra virgin olive oil
- Avocado oil
- Coconut oil
- Ghee
- Lard
- Any other animal-based fats
Key Design Requirements:
- Clarity and speed of communication: The card should be easily read and understood by waiters, even in low-light environments, emphasizing that it's a health concern.
- Avoid common misconceptions: Ensure the design doesn't imply common dietary preferences like "vegetarian" or "no butter." Animal fats and butter are actually preferable for her!
- Preferred term: Use "seed oils" as the term to describe what she cannot eat due to her health issue.
- Trace amounts are acceptable: Communicate that it's OK to use cookware that has previously been in contact with seed oils, but not to have seed oil as an ingredient. Please suggest a concise way to convey this.
- Card dimensions: Design should be 3.5” x 2.25” (standard credit-card size on printorvale.example). Horizontal or vertical layouts are both fine, whichever makes the message clearer.
Design Suggestions:
- Utilize bold and easy-to-read typography to communicate the main message.
- Consider incorporating relevant icons or graphics that help convey the message without adding confusion.
- Use contrasting colors to enhance readability, especially in low-light situations.
- To communicate the “trace amounts OK” part, consider phrases such as:
- "Cross-contamination acceptable"
- “Used cookware OK, no ingredient use”
- “Separate cookware not necessary”
Thank you for your assistance in creating this essential card for my wife's health and safety when dining out!

```html
<!DOCTYPE html>
<html lang="en">
<head>
<meta charset="utf-8">
<title>Health-Related Dietary Restriction Card</title>
<link rel="stylesheet" href="https://fonts.googleapis.com/css2?family=Open+Sans:ital,wght@0,400;0,600;0,700;1,400&display=swap">
<style>
  :root {
    --bg: #dcdde0;
    --blue: #1a6db0;
    --red: #cc1f2e;
    --green: #5c9e2e;
    --brown: #6a4522;
    --ink: #1f1f1f;
    --white: #ffffff;
  }
  * { margin: 0; padding: 0; box-sizing: border-box; }
  html, body {
    width: 1200px; height: 2743px; overflow: hidden;
    background: var(--bg);
    font-family: "Open Sans", Arial, sans-serif;
  }
  .card {
    position: absolute; left: 100px; top: 593px;
    width: 1000px; height: 1556px;
    background: var(--white);
    border-radius: 48px; overflow: hidden;
    box-shadow: 6px 10px 18px rgba(0,0,0,0.35);
  }
  .card-header {
    position: absolute; left: 0; top: 0; width: 100%; height: 212px;
    background: var(--blue); color: var(--white); text-align: center;
  }
  .card-header .kicker {
    position: absolute; top: 38px; width: 100%;
    font-size: 56px; font-weight: 400; letter-spacing: 17px; line-height: 1;
  }
  .card-header .title {
    position: absolute; top: 104px; width: 100%;
    font-size: 70px; font-weight: 700; line-height: 1;
  }
  .icon { position: absolute; width: 85px; height: 85px; }
  .icon-no { left: 47px; top: 263px; }
  .icon-ok { left: 47px; top: 887px; }
  .heading {
    position: absolute; left: 156px;
    font-size: 41px; font-weight: 700; line-height: 49px; color: var(--ink);
  }
  .heading-no { top: 240px; }
  .heading-ok { top: 878px; }
  .heading .warn { color: var(--red); }
  .heading .safe { color: var(--green); }
  .oil-list {
    position: absolute; list-style: none;
    font-size: 52px; line-height: 62px; color: var(--brown);
  }
  .oil-list li::before {
    content: "•"; display: inline-block; width: 44px; color: var(--ink);
  }
  .list-left { left: 66px; top: 405px; }
  .list-right { left: 523px; top: 405px; }
  .list-safe { left: 66px; top: 998px; }
  .divider {
    position: absolute; left: 459px; top: 414px;
    width: 7px; height: 290px; background: var(--red);
  }
  .trace-note {
    position: absolute; left: 48px; top: 735px;
    font-size: 44px; font-style: italic; line-height: 50px; color: var(--ink);
  }
  .trace-note span { display: block; padding-left: 17px; }
  .trace-note span:first-child { padding-left: 0; }
  .oil-illustration {
    position: absolute; left: 470px; top: 951px;
    width: 520px; height: 450px; border-radius: 50%;
    background: radial-gradient(ellipse at 55% 45%, #f4e7b8 0%, #efe3c6 45%, rgba(255,255,255,0) 72%);
  }
  .card-footer {
    position: absolute; left: 0; bottom: 0; width: 100%; height: 88px;
    background: var(--blue); color: var(--white);
    font-size: 34px; font-weight: 700; letter-spacing: 5px;
    text-align: center; line-height: 88px;
  }
</style>
</head>
<body>
  <section class="card">
    <header class="card-header">
      <div class="kicker">HEALTH-RELATED</div>
      <div class="title">DIETARY RESTRICTION</div>
    </header>

    <svg class="icon icon-no" viewBox="0 0 100 100" aria-hidden="true">
      <circle cx="50" cy="50" r="48" fill="#cc1f2e"/>
      <path d="M32 32 L68 68 M68 32 L32 68" stroke="#fff" stroke-width="13" stroke-linecap="round"/>
    </svg>
    <p class="heading heading-no">PLEASE MAKE SURE THAT MY<br>MEALS ARE PREPARED WITHOUT<br>ANY <span class="warn">SEED OILS/PROCESSED OILS</span>:</p>

    <ul class="oil-list list-left">
      <li>Vegetable oil</li>
      <li>Canola oil</li>
      <li>Soybean oil</li>
      <li>Sunflower oil</li>
      <li>Corn oil</li>
    </ul>
    <div class="divider"></div>
    <ul class="oil-list list-right">
      <li>Cottonseed oil</li>
      <li>Safflower oil</li>
      <li>Peanut oil</li>
      <li>Sesame oil</li>
    </ul>

    <p class="trace-note"><span>*Trace amounts are acceptable</span><span>Separate cookwares are not necessary</span></p>

    <svg class="icon icon-ok" viewBox="0 0 100 100" aria-hidden="true">
      <circle cx="50" cy="50" r="48" fill="#5c9e2e"/>
      <path d="M27 52 L44 68 L74 34" fill="none" stroke="#fff" stroke-width="12" stroke-linecap="round" stroke-linejoin="round"/>
    </svg>
    <p class="heading heading-ok"><span class="safe">OTHER OILS</span> THAT ARE SAFE<br>TO USE:</p>

    <div class="oil-illustration" role="img" aria-label="Illustration of a corked glass bottle of oil beside a pile of seeds and small leaves"></div>

    <ul class="oil-list list-safe">
      <li>Butter (most preferable)</li>
      <li>Extra virgin olive oil</li>
      <li>Avocado oil</li>
      <li>Coconut oil</li>
      <li>Ghee</li>
      <li>Lard</li>
      <li>Any other animal-based fats</li>
    </ul>

    <footer class="card-footer">THANK YOU FOR KEEPING ME SAFE</footer>
  </section>
</body>
</html>
```